Exciting & Elegant Stationary Pack

Stationary consists of
1. Letter head / Envelope
2. Business Card
3. Invoice
4. 40x40mm sticker

Attached files;

1. Logo (Other formats available on request)
2. MS word Doc - For information and description of design
3. Website image (This will be our new website so use the colours so everything ties together)
4. Sample of stationary pack we like, but feel free to be creative

Target Market(s)

Home improvement

Industry/Entity Type

Construction

Font styles to use
Other font styles liked:
• Leave up to designer - We like font used on (website attached image)

Requirements
Must have
• Please look at uploaded file of sample website and use colours
Nice to have
• Any type of business card design - eg. metal, die cut, embossed, etc...

```html
<!DOCTYPE html>
<html lang="en">
<head>
<meta charset="utf-8">
<title>Tessera Trades – Stationery Pack</title>
<link rel="stylesheet" href="https://fonts.googleapis.com/css2?family=Source+Sans+3:wght@400;600;700&display=swap">
<style>
:root{
  --navy:#154673;
  --red:#d0252f;
  --sky:#9cc3e5;
  --paper:#f1f0ef;
  --white:#ffffff;
  --stage:#a9a8a9;
  --ink:#3c4a5a;
  --rule:#2f6390;
  --stripe:#cdd6e0;
}
*{box-sizing:border-box;margin:0;padding:0}
html,body{width:1200px;height:838px;overflow:hidden}
body{background:var(--stage);font-family:"Source Sans 3",sans-serif;color:var(--ink);position:relative}
.sheet{position:absolute;background:var(--paper);box-shadow:0 1px 3px rgba(0,0,0,.35);overflow:hidden}
.band{position:absolute;left:0;right:0}
.band--red{background:var(--red)}
.band--sky{background:var(--sky)}
.brand{position:absolute;font-weight:700;color:var(--navy);letter-spacing:.04em;white-space:nowrap;display:flex;align-items:center;gap:6px;line-height:1}
.brand__dot{display:inline-block;background:var(--navy);flex:none}
.brand--light{color:var(--white)}
.brand--light .brand__dot{background:var(--white)}
.meta{position:absolute;color:var(--white);font-size:7px;white-space:nowrap}
.contact{position:absolute;font-size:7.3px;color:var(--navy);display:flex;align-items:center;gap:4px;white-space:nowrap}
.contact svg{width:7px;height:8px;fill:var(--navy);flex:none}

/* cover */
.cover{left:44px;top:50px;width:376px;height:530px;background:var(--navy)}

/* letter */
.letter{left:435px;top:91px;width:348px;height:490px}
.letter__greeting{position:absolute;left:26px;top:138px;font-size:9.5px}
.letter__body{position:absolute;left:26px;top:167px;width:302px;font-size:5.3px;line-height:8.4px;text-align:justify}
.letter__body p{margin-bottom:8.4px}
.letter__sign{position:absolute;left:26px;top:343px;font-size:4.8px;line-height:9px}
.letter__name{position:absolute;left:38px;top:378px;font-size:5px;line-height:9px}

/* invoice */
.invoice{left:807px;top:91px;width:348px;height:490px}
.field{position:absolute;font-size:5.5px;line-height:6px;color:var(--navy);display:flex;align-items:flex-end;gap:3px}
.field span.line{flex:1;border-bottom:.7px solid var(--rule);height:5px}
.field--label{font-weight:700}
.ledger{position:absolute;left:25px;top:172px;width:296px;height:229px;border:1px solid var(--rule);
  background:repeating-linear-gradient(to bottom,var(--stripe) 0 13.4px,var(--paper) 13.4px 26.8px)}
.ledger__head{position:absolute;left:0;right:0;top:0;height:15px;background:var(--navy);color:var(--white);font-size:5.3px;font-weight:700}
.ledger__head span{position:absolute;top:4px}
.ledger__col{position:absolute;top:0;bottom:0;border-left:1px solid var(--rule)}
.payments{position:absolute;font-size:5.5px;font-weight:600;color:var(--navy)}
.totals{position:absolute;left:244px;top:414px;width:77px;border:1px solid var(--rule)}
.totals div{height:14px;border-bottom:1px solid var(--rule);display:flex;font-size:5.3px;font-weight:700;color:var(--navy)}
.totals div:last-child{border-bottom:none}
.totals b{width:48px;border-right:1px solid var(--rule);display:flex;align-items:center;justify-content:center}
.invoice__note{position:absolute;left:25px;top:461px;font-size:4.6px;line-height:6px}

/* cards */
.card{left:46px;top:595px;width:152px;height:87px;background:var(--white)}
.card__role{position:absolute;right:10px;top:41px;text-align:right;color:var(--white);font-size:5.5px;font-weight:700;line-height:5.5px}
.card__role small{display:block;font-size:3.6px;font-weight:400}
.card__info{position:absolute;right:10px;top:58px;text-align:right;font-size:3.8px;line-height:6px;color:var(--navy)}
.card-back{left:42px;top:694px;width:153px;height:87px;background:var(--navy)}

/* envelopes */
.envelope{left:211px;top:603px;width:391px;height:178px}
.envelope-back{left:614px;top:605px;width:392px;height:178px}
.envelope-back__flap{position:absolute;left:0;right:0;top:0;height:57px;background:var(--navy);border-radius:0 0 14px 14px}

/* sticker */
.sticker{left:1025px;top:623px;width:156px;height:157px;background:var(--white)}
.sticker__info{position:absolute;right:12px;text-align:right;font-size:6.5px;line-height:10px;color:var(--navy)}
.sticker__info div{display:flex;justify-content:flex-end;align-items:center;gap:4px}
.sticker__info svg{width:6px;height:7px;fill:var(--navy)}
</style>
</head>
<body>

<svg width="0" height="0" style="position:absolute">
  <defs>
    <symbol id="icon-phone" viewBox="0 0 8 10"><path d="M1 0h6v10H1zM2 1v7h4V1z"/></symbol>
    <symbol id="icon-pin" viewBox="0 0 8 10"><path d="M4 0a3.5 3.5 0 0 1 3.5 3.5C7.5 6 4 10 4 10S.5 6 .5 3.5A3.5 3.5 0 0 1 4 0zm0 2a1.5 1.5 0 1 0 0 3 1.5 1.5 0 0 0 0-3z"/></symbol>
    <symbol id="icon-web" viewBox="0 0 10 10"><circle cx="5" cy="5" r="5"/></symbol>
  </defs>
</svg>

<!-- Folder cover -->
<section class="sheet cover" role="img" aria-label="Navy folder cover with tile texture">
  <div class="brand brand--light" style="left:112px;top:62px;font-size:22px;gap:5px"><span class="brand__dot" style="width:9px;height:9px"></span>TESSERA TRADES</div>
  <div class="band band--red" style="top:143px;height:50px"></div>
  <div class="band band--sky" style="top:193px;height:50px"></div>
</section>

<!-- Letterhead -->
<section class="sheet letter">
  <div class="brand" style="right:20px;top:38px;font-size:13px"><span class="brand__dot" style="width:7px;height:7px"></span>TESSERA TRADES</div>
  <div class="band band--red" style="top:60px;height:20px"></div>
  <div class="band band--sky" style="top:80px;height:21px"></div>
  <div class="meta" style="left:27px;top:66px">ABN : 12 345 678 901</div>
  <div class="contact" style="left:36px;top:87px">
    <svg><use href="#icon-phone"/></svg>0400 555 017
    <svg><use href="#icon-pin"/></svg>PO BOX 48 GREENVALE NSW 2170
    <svg><use href="#icon-web"/></svg>www.tesseratrades.com.au
  </div>
  <div class="letter__greeting">Dear Mr. Carter,</div>
  <div class="letter__body">
    <p>We are pleased to confirm our quote for the bathroom and kitchen tiling at your home. Our team will arrive on the agreed date with all materials, protect your floors and fittings, and remove old tiles and adhesive before setting out the new layout. Every surface is checked for level and moisture so the finish lasts for many years.</p>
    <p>Wall tiles will be set with a fine grout line and sealed at all wet edges. Floor tiles will be laid over a waterproof membrane, with falls to each drain, and cut neatly around every fixture.</p>
    <p>Once the work is done we clean the site, walk through each room with you and note any item you would like changed. A written warranty covers labour and waterproofing for seven years.</p>
    <p>Please call our office if you have any questions or wish to change the start date.</p>
  </div>
  <div class="letter__sign">Sincerely,</div>
  <svg style="position:absolute;left:36px;top:355px" width="50" height="16" viewBox="0 0 50 16"><path d="M2 9 C12 2 20 4 28 8 S42 10 48 7 M30 4 L34 14" stroke="#222" stroke-width=".8" fill="none"/></svg>
  <div class="letter__name">Dan Ellis<br>CEO/ Founder</div>
</section>

<!-- Invoice -->
<section class="sheet invoice">
  <div class="brand" style="right:20px;top:38px;font-size:13px"><span class="brand__dot" style="width:7px;height:7px"></span>TESSERA TRADES</div>
  <div class="band band--red" style="top:60px;height:20px"></div>
  <div class="band band--sky" style="top:80px;height:21px"></div>
  <div class="meta" style="left:28px;top:66px">ABN : 12 345 678 901</div>
  <div class="contact" style="left:30px;top:87px">
    <svg><use href="#icon-phone"/></svg>0400 555 017
    <svg><use href="#icon-pin"/></svg>PO BOX 48 GREENVALE NSW 2170
    <svg><use href="#icon-web"/></svg>www.tesseratrades.com.au
  </div>
  <div class="field field--label" style="left:25px;top:124px">INVOICE # :</div>
  <div class="field field--label" style="left:248px;top:124px">DATE :</div>
  <div class="field" style="left:25px;top:137px;width:296px">Customer:<span class="line"></span></div>
  <div class="field" style="left:25px;top:149px;width:296px">Address :<span class="line"></span></div>
  <div class="field" style="left:25px;top:161px;width:148px">Phone :<span class="line"></span></div>
  <div class="field" style="left:182px;top:161px;width:139px">Fax :<span class="line"></span></div>

  <div class="ledger">
    <div class="ledger__col" style="left:25px"></div>
    <div class="ledger__col" style="left:218px"></div>
    <div class="ledger__col" style="left:257px"></div>
    <div class="ledger__head">
      <span style="left:6px">QTY</span>
      <span style="left:94px">DESCRIPTION</span>
      <span style="left:228px">PRICE</span>
      <span style="left:262px">AMOUNT</span>
    </div>
  </div>
  <div class="payments" style="left:37px;top:424px">VISA</div>
  <div class="payments" style="left:76px;top:424px">MC</div>
  <div class="payments" style="left:109px;top:424px">DEBIT</div>
  <div class="payments" style="left:156px;top:424px">CASH</div>
  <div class="payments" style="left:203px;top:424px">CHEQUE</div>
  <div class="totals">
    <div><b>SUB TOTAL</b></div>
    <div><b>GST #</b></div>
    <div><b>SUBTOTAL</b></div>
  </div>
  <div class="invoice__note">Signature Indicates<br>Acceptance of Price and term</div>
</section>

<!-- Business card front -->
<section class="sheet card">
  <div class="brand" style="left:10px;top:16px;font-size:8.5px;gap:3px"><span class="brand__dot" style="width:4px;height:4px"></span>TESSERA TRADES</div>
  <div class="band band--red" style="top:39px;height:16px"></div>
  <div class="band band--sky" style="top:55px;bottom:0"></div>
  <div class="card__role">Leo Marsh<small>Project Manager</small></div>
  <div class="card__info">Lic No. 204118C<br>0400 555 017 ▯<br>info@tesseratrades.com.au ■<br>www.tesseratrades.com.au ●</div>
</section>

<!-- Business card back -->
<section class="sheet card-back" role="img" aria-label="Navy card back with tile texture">
  <div style="position:absolute;right:0;top:40px;width:62px;bottom:0;background:var(--white)"></div>
  <div class="brand" style="right:5px;top:58px;font-size:5.5px;gap:2px;letter-spacing:.02em"><span class="brand__dot" style="width:3px;height:3px"></span>TESSERA TRADES</div>
</section>

<!-- DL envelope front -->
<section class="sheet envelope">
  <div class="brand" style="left:74px;top:27px;font-size:15px"><span class="brand__dot" style="width:7px;height:7px"></span>TESSERA TRADES</div>
  <div class="band band--red" style="top:50px;height:21px"></div>
  <div class="band band--sky" style="top:71px;height:21px"></div>
  <div class="contact" style="left:27px;top:78px"><svg><use href="#icon-pin"/></svg>PO BOX 48 GREENVALE NSW 2170</div>
</section>

<!-- DL envelope back -->
<section class="sheet envelope-back">
  <div class="envelope-back__flap"></div>
  <div class="brand brand--light" style="left:162px;top:16px;font-size:9.5px;gap:3px"><span class="brand__dot" style="width:4px;height:4px"></span>TESSERA TRADES</div>
</section>

<!-- 40x40 sticker -->
<section class="sheet sticker">
  <div class="brand" style="left:20px;top:53px;font-size:12.5px;gap:4px"><span class="brand__dot" style="width:5px;height:5px"></span>TESSERA TRADES</div>
  <div class="band band--red" style="top:83px;height:24px"></div>
  <div class="band band--sky" style="top:107px;bottom:0"></div>
  <div class="sticker__info" style="top:113px">
    <div>0400 555 017 <svg><use href="#icon-phone"/></svg></div>
    <div>PO Box 48 Greenvale NSW 2170 <svg><use href="#icon-pin"/></svg></div>
  </div>
</section>

</body>
</html>
```